Business card design for a dynamic IT consulting company

We need a business card design for a young firm, specialized in the Telecommunications/Consulting industry. The name of the company is Quindor and Partners Business Consulting Ltd. (Short name: Quindor and Partnes)
Quindor = solve read reverse, so we aim to be uncomplicated and solution-oriented. The small pipe in our logo is also related to the word solve. So we need a new business card design, which is simple, eye catching and something non traditional (I would probably prefer a square shaped design rather than a rectangle, but open for suggestions). Attached our logo.

Target Market(s)

Usually our customers are Tier1 Telecoms providers (Q-Netra, Palorix, etc) and their executives.

Industry/Entity Type

Business

Contact Information for Business Card

Name: Bence Tolnavari
Email: b.tolnavari@quindor.hu
Web: www.quindor.hu
Mobile: +36 30 518 2769
Title: Managing Director

Optional:
Company name: Quindor and Partners Ltd.
Address: 1087 Budapest, Tolvenka str. 28/C, Hungary

Font styles to use
Other font styles liked:
• helveticaneue_medium, Prime Regular are used now.

Colors

Designer to choose colors to be used in the design.

Requirements
Must have
• I would like to have a 2 sided design.
Nice to have
• I thought if we make the logo a bit bigger (without the company name), that could go to the back with the company name below. I though, if the pipe in the logo is somehow touchable on the business card, would be nice and unique.

```html
<!DOCTYPE html>
<html lang="en">
<head>
<meta charset="UTF-8">
<title>Quindor and Partners – Business Card</title>
<link rel="stylesheet" href="https://fonts.googleapis.com/css2?family=Roboto:wght@400;500;700&display=swap">
<style>
  :root {
    --bg: #151515;
    --card-white: #f4f4f5;
    --card-black: #1c1c1e;
    --ink: #4a4a4c;
    --ink-soft: #77777a;
    --rule: #9a9a9c;
    --blue: #2a9ad6;
    --magenta: #b23a9a;
    --band: #1f1f21;
    --white: #ffffff;
  }
  * { margin: 0; padding: 0; box-sizing: border-box; }
  html, body {
    width: 1200px; height: 900px; overflow: hidden;
    background: var(--bg);
    font-family: "Roboto", Arial, sans-serif;
  }
  .sheet { position: relative; width: 1200px; height: 900px; }

  .card {
    position: absolute; left: 250px; width: 700px; height: 400px;
    border-radius: 18px; overflow: hidden;
  }
  .card--front { top: 35px; background: var(--card-white); }
  .card--back { top: 465px; background: var(--card-black); }

  /* brand name */
  .brand { display: flex; align-items: center; gap: 14px; font-weight: 500; }
  .brand__mark { width: 14px; height: 14px; background: var(--blue); }
  .card--front .brand { position: absolute; left: 70px; top: 42px; font-size: 36px; color: var(--ink); }

  /* identity */
  .person { position: absolute; left: 46px; top: 118px; }
  .person__name { font-size: 31px; font-weight: 700; color: var(--blue); }
  .person__title { font-size: 20px; font-weight: 400; color: var(--ink-soft); margin-top: 4px; }
  .rule { position: absolute; left: 40px; right: 40px; top: 198px; height: 1px; background: var(--rule); }

  .contacts { position: absolute; left: 40px; top: 214px; list-style: none; }
  .contacts__item { display: flex; align-items: center; gap: 10px; font-size: 17px; color: var(--ink); margin-bottom: 9px; }
  .contacts__icon { width: 22px; height: 22px; border-radius: 50%; display: flex; align-items: center; justify-content: center; }
  .contacts__icon--phone { background: var(--magenta); }
  .contacts__icon--mail { background: var(--blue); }

  .address {
    position: absolute; right: 46px; bottom: 84px; text-align: right;
    font-size: 18px; line-height: 1.35; color: var(--ink);
  }

  .accent-band {
    position: absolute; left: 0; right: 0; bottom: 0; height: 58px;
    background: linear-gradient(90deg, var(--magenta) 0%, var(--blue) 40%, var(--band) 70%);
  }
  .card--front .web {
    position: absolute; right: 46px; bottom: 18px;
    font-size: 17px; font-weight: 500; color: var(--white);
  }

  /* back */
  .card--back .brand {
    position: absolute; left: 0; right: 0; top: 150px; justify-content: center;
    font-size: 48px; color: #e2e2e4;
  }
  .card--back .web {
    position: absolute; left: 0; right: 0; top: 250px; text-align: center;
    font-size: 18px; color: #a9a9ac;
  }
</style>
</head>
<body>
<main class="sheet">

  <section class="card card--front" aria-label="Business card front">
    <div class="accent-band" role="img" aria-label="Decorative curved band in magenta, blue and black along the lower edge"></div>

    <div class="brand"><span class="brand__mark"></span><span class="brand__name">Quindor &amp; Partners</span></div>

    <div class="person">
      <h1 class="person__name">Bence Tolnavari</h1>
      <p class="person__title">Managing Director</p>
    </div>
    <div class="rule"></div>

    <ul class="contacts">
      <li class="contacts__item">
        <span class="contacts__icon contacts__icon--phone">
          <svg width="12" height="12" viewBox="0 0 24 24" aria-hidden="true"><path fill="#fff" d="M6.6 10.8a15 15 0 0 0 6.6 6.6l2.2-2.2c.3-.3.7-.4 1-.2 1.1.4 2.3.6 3.6.6.6 0 1 .4 1 1V20c0 .6-.4 1-1 1A17 17 0 0 1 3 4c0-.6.4-1 1-1h3.5c.6 0 1 .4 1 1 0 1.3.2 2.5.6 3.6.1.3 0 .7-.2 1z"/></svg>
        </span>
        +36 30 518 2769
      </li>
      <li class="contacts__item">
        <span class="contacts__icon contacts__icon--mail">
          <svg width="12" height="12" viewBox="0 0 24 24" aria-hidden="true"><path fill="#fff" d="M3 5h18v14H3z"/><path fill="none" stroke="#2a9ad6" stroke-width="2" d="M3 6l9 7 9-7"/></svg>
        </span>
        b.tolnavari@quindor.hu
      </li>
    </ul>

    <p class="address">1087 Budapest,<br>Tolvenka str. 28/C, Hungary</p>
    <p class="web">www.quindor.hu</p>
  </section>

  <section class="card card--back" aria-label="Business card back">
    <div class="brand"><span class="brand__mark"></span><span class="brand__name">Quindor &amp; Partners</span></div>
    <p class="web">www.quindor.hu</p>
  </section>

</main>
</body>
</html>
```